Business Name: K&M Group Cleaning Services - Cleaning business

We need a website to be able to get our services out to the market..
We have just invested over $60,000 in our new van which is capable of doing specialised cleaning services see attached flyer... I will also send through our company logo....We do all types of cleaning from move out cleans, office cleans and have the capability fire flood and restoration services as well
On the flyer it has Desmond as a contact do not use his name only use Glenn as a contact
Want some good pictures included
Prefer people to contact me via email rather than calling me.

```html
<!DOCTYPE html>
<html lang="en">
<head>
<meta charset="utf-8">
<title>K&amp;M Group Cleaning Services</title>
<link href="https://fonts.googleapis.com/css2?family=Lato:wght@400;700;900&family=Open+Sans:wght@400;600&display=swap" rel="stylesheet">
<style>
:root{
  --orange:#f26522;
  --orange-deep:#e2561a;
  --ink:#222222;
  --text:#444444;
  --muted:#777777;
  --line:#dddddd;
  --white:#ffffff;
}
*{box-sizing:border-box;margin:0;padding:0}
html,body{width:1200px;height:3267px;overflow:hidden;background:var(--white)}
body{position:relative;font-family:"Open Sans",Arial,sans-serif;color:var(--text)}
.heading{font-family:"Lato",Arial,sans-serif;font-weight:900;text-transform:uppercase}
.btn{position:absolute;display:flex;align-items:center;justify-content:center;border-radius:40px;font-family:"Lato",Arial,sans-serif;font-weight:900;text-transform:uppercase;letter-spacing:.5px}
.btn--orange{background:var(--orange);color:var(--white)}
.btn--white{background:var(--white);color:var(--orange)}

/* header */
.site-header{position:absolute;left:0;top:0;width:1200px;height:115px;background:var(--white)}
.brand{position:absolute;left:150px;top:22px;display:flex;align-items:center;gap:16px}
.brand__mark{width:72px;height:72px;border:3px solid var(--orange);border-radius:50%}
.brand__name{font-family:"Lato",Arial,sans-serif;font-weight:700;font-size:25px;letter-spacing:2px;color:var(--ink)}
.nav{position:absolute;left:414px;top:47px;display:flex;gap:27px;font-family:"Lato",Arial,sans-serif;font-weight:700;font-size:15.5px;color:var(--ink)}
.header-contact{position:absolute;left:900px;top:34px;display:flex;align-items:center;gap:9px;font-family:"Lato",Arial,sans-serif;color:var(--ink)}
.header-contact__lines{display:flex;flex-direction:column;line-height:20px}
.header-contact__label{font-size:12px;font-weight:700;color:var(--orange);text-transform:uppercase;letter-spacing:.5px}
.header-contact__email{font-size:16px;font-weight:700}

/* hero */
.hero{position:absolute;left:0;top:115px;width:1200px;height:603px;
  background:linear-gradient(90deg,#6c7867 0%,#8d9380 30%,#7a7f74 55%,#4e6b52 80%,#6f8aa6 100%)}
.hero__shade{position:absolute;inset:0;background:rgba(0,0,0,.28)}
.hero__ring{position:absolute;left:549px;top:127px;width:104px;height:104px;border:4px solid var(--white);border-radius:50%}
.hero__title{position:absolute;left:0;top:240px;width:1200px;text-align:center;color:var(--white);font-size:50px;line-height:55px}
.hero__arrow{position:absolute;top:264px;width:52px;height:52px;border-radius:50%;background:rgba(255,255,255,.35)}

/* about */
.about__photo{position:absolute;left:0;top:817px;width:523px;height:413px;border-radius:0 207px 207px 0;
  background:linear-gradient(135deg,#c4562e 0%,#d96a3c 45%,#b8482a 100%)}
.about__title{position:absolute;left:551px;top:840px;font-size:36px;color:var(--ink);font-weight:700}
.about__title span{color:var(--orange)}
.about__text{position:absolute;left:551px;top:905px;width:540px;font-size:17.5px;line-height:26px;color:var(--text)}
.about__text p+p{margin-top:20px}

/* specialise */
.specialise{position:absolute;left:0;top:1307px;width:1200px;height:527px;
  background:linear-gradient(90deg,var(--orange) 0%,var(--orange) 42%,#d9834f 58%,#c8a883 75%,#ded7cb 100%)}
.specialise__title{position:absolute;left:157px;top:86px;font-size:31px;color:var(--white);font-weight:700}
.specialise__list{position:absolute;left:157px;top:148px;list-style:none;color:var(--white);font-size:17px;line-height:33.5px}
.specialise__list li{display:flex;align-items:center;gap:10px}

/* services */
.services__title{position:absolute;left:0;top:1883px;width:1200px;text-align:center;font-size:31px;color:var(--ink)}
.card{position:absolute;top:1950px;width:273px;height:368px;background:var(--white);box-shadow:0 1px 5px rgba(0,0,0,.25)}
.card__photo{height:185px}
.card__title{margin-top:22px;text-align:center;font-family:"Lato",Arial,sans-serif;font-weight:900;font-size:17px;line-height:21px;color:var(--orange);text-transform:uppercase;padding:0 20px}
.card__text{margin:6px auto 0;width:215px;text-align:center;font-size:11.5px;line-height:15px;color:var(--muted)}
.card .btn{left:71px;bottom:24px;width:131px;height:44px;font-size:13px}

/* call to action */
.cta{position:absolute;left:0;top:2413px;width:1200px;height:469px;
  background:linear-gradient(90deg,#3c3c3c 0%,#5a5a58 45%,#4a4a48 70%,#3a3a3a 100%)}
.cta__ring{position:absolute;left:673px;top:42px;width:340px;height:340px;border:12px solid var(--orange);border-radius:50%}
.cta__title{position:absolute;left:172px;top:118px;font-size:31px;line-height:37px;color:var(--white);font-weight:700}
.cta__text{position:absolute;left:172px;top:242px;width:440px;font-size:17.5px;line-height:24px;color:var(--white)}

/* footer */
.footer-brand{position:absolute;left:200px;top:2952px;width:145px;display:flex;flex-direction:column;align-items:center;gap:14px}
.footer-brand .brand__mark{width:96px;height:96px}
.footer-col{position:absolute;top:2946px}
.footer-col h3{font-family:"Lato",Arial,sans-serif;font-weight:900;font-size:17px;color:var(--orange);text-transform:uppercase;margin-bottom:12px}
.footer-col li{list-style:none;font-size:14px;line-height:30px;color:var(--text)}
.footer-col .footer-email{color:var(--orange);font-weight:600}
.social li{display:flex;align-items:center;gap:10px;line-height:33px}
.social__dot{width:28px;height:28px;border-radius:50%;border:2px solid var(--orange)}
.footer-rule{position:absolute;left:0;top:3195px;width:1200px;height:1px;background:var(--line)}
.copyright{position:absolute;left:0;top:3216px;width:1200px;text-align:center;font-size:14px;color:var(--text)}
</style>
</head>
<body>

<header class="site-header">
  <div class="brand"><div class="brand__mark"></div><span class="brand__name">KM GROUP</span></div>
  <nav class="nav"><span>ABOUT US</span><span>OUR SERVICES</span><span>BLOGS</span><span>WHY US</span><span>CONTACT</span></nav>
  <div class="header-contact">
    <svg width="24" height="18" viewBox="0 0 24 18"><rect x="1" y="1" width="22" height="16" rx="2" fill="none" stroke="#f26522" stroke-width="2"/><path d="M2 2l10 8 10-8" fill="none" stroke="#f26522" stroke-width="2"/></svg>
    <div class="header-contact__lines">
      <span class="header-contact__label">Email Glenn</span>
      <span class="header-contact__email">glenn@kmgroup.example</span>
    </div>
  </div>
</header>

<section class="hero" role="img" aria-label="Photo of a worker pressure cleaning a garden path outside a house">
  <div class="hero__shade"></div>
  <div class="hero__ring"></div>
  <h1 class="hero__title heading">High Pressure<br>Cleaning Services</h1>
  <div class="btn btn--orange" style="left:508px;top:369px;width:187px;height:65px;font-size:19px">Contact Us</div>
  <div class="hero__arrow" style="left:126px">
    <svg width="52" height="52" viewBox="0 0 52 52"><path d="M30 17l-9 9 9 9" stroke="#333" stroke-width="3" fill="none"/></svg>
  </div>
  <div class="hero__arrow" style="left:1013px">
    <svg width="52" height="52" viewBox="0 0 52 52"><path d="M22 17l9 9-9 9" stroke="#333" stroke-width="3" fill="none"/></svg>
  </div>
</section>

<section class="about">
  <div class="about__photo" role="img" aria-label="Photo of a worker cleaning an orange tiled roof"></div>
  <h2 class="about__title heading">About <span>KM Group</span></h2>
  <div class="about__text">
    <p>Whether you need to clean your existing premises or even remove graffiti, our commercial cleaning solutions go above and beyond when it comes to restoring your premises.</p>
    <p>We have extensive experience and work closely with Councils, Recreational Parks, Real Estate Agents, The Department of Public Services, High profile retail shops and more.</p>
  </div>
  <div class="btn btn--orange" style="left:547px;top:1124px;width:174px;height:57px;font-size:18px">Read More</div>
</section>

<section class="specialise" role="img" aria-label="Photo of two cleaners wiping a table and mopping a floor">
  <h2 class="specialise__title heading">What We Specialise In</h2>
  <ul class="specialise__list">
    <li><svg width="10" height="14" viewBox="0 0 10 14"><path d="M2 1l6 6-6 6" stroke="#fff" stroke-width="3" fill="none"/></svg>Pressure clean driveways and seals</li>
    <li><svg width="10" height="14" viewBox="0 0 10 14"><path d="M2 1l6 6-6 6" stroke="#fff" stroke-width="3" fill="none"/></svg>Tile and grout clean</li>
    <li><svg width="10" height="14" viewBox="0 0 10 14"><path d="M2 1l6 6-6 6" stroke="#fff" stroke-width="3" fill="none"/></svg>Commercial and residential carpet/upholstery cleaning</li>
    <li><svg width="10" height="14" viewBox="0 0 10 14"><path d="M2 1l6 6-6 6" stroke="#fff" stroke-width="3" fill="none"/></svg>Gutter cleaning</li>
    <li><svg width="10" height="14" viewBox="0 0 10 14"><path d="M2 1l6 6-6 6" stroke="#fff" stroke-width="3" fill="none"/></svg>Fire and flood restoration capability</li>
    <li><svg width="10" height="14" viewBox="0 0 10 14"><path d="M2 1l6 6-6 6" stroke="#fff" stroke-width="3" fill="none"/></svg>End of lease cleaning - no power required</li>
  </ul>
  <div class="btn btn--white" style="left:148px;top:370px;width:170px;height:57px;font-size:18px">Read More</div>
</section>

<section class="services">
  <h2 class="services__title heading">Our Services</h2>
  <article class="card" style="left:170px">
    <div class="card__photo" role="img" aria-label="Photo of moving boxes and cleaning supplies in an empty room" style="background:linear-gradient(135deg,#e6e2dc,#b8a48a)"></div>
    <h3 class="card__title">Move Out Cleaning</h3>
    <p class="card__text">Duis non nunc Nulla rhoncus dictum metus Curabitur tristique mi condimentum orci Phasellus pellentesq</p>
    <div class="btn btn--orange">Read More</div>
  </article>
  <article class="card" style="left:468px">
    <div class="card__photo" role="img" aria-label="Photo of two cleaners in uniform inside an office" style="background:linear-gradient(135deg,#d8d6d2,#6a7fa8)"></div>
    <h3 class="card__title">Office Cleaning</h3>
    <p class="card__text">Duis non nunc Nulla rhoncus dictum metus Curabitur tristique mi condimentum orci Phasellus pellentesq</p>
    <div class="btn btn--orange">Read More</div>
  </article>
  <article class="card" style="left:760px">
    <div class="card__photo" role="img" aria-label="Photo of a floor machine cleaning a flooded hall" style="background:linear-gradient(135deg,#c9c6c0,#77726a)"></div>
    <h3 class="card__title">Fire Flood and<br>Restoration</h3>
    <p class="card__text">Duis non nunc Nulla rhoncus dictum metus Curabitur tristique</p>
    <div class="btn btn--orange">Read More</div>
  </article>
</section>

<section class="cta" role="img" aria-label="Photo of a floor scrubbing machine in use">
  <div class="cta__ring"></div>
  <h2 class="cta__title heading">For the highest<br>performance and<br>durability,choose us!</h2>
  <p class="cta__text">Lorem ipsum dolor sit amet consectetuer adipiscing elit Nam cursus Morbi ut mi Nullam enim</p>
  <div class="btn btn--white" style="left:168px;top:306px;width:168px;height:57px;font-size:18px">Read More</div>
</section>

<footer>
  <div class="footer-brand"><div class="brand__mark"></div><span class="brand__name" style="font-size:22px">KM GROUP</span></div>
  <div class="footer-col" style="left:416px">
    <h3>Contact Us</h3>
    <ul>
      <li>K &amp; M GROUP CLEANING SERVICES PTY LTD</li>
      <li>Contact: Glenn</li>
      <li class="footer-email">glenn@kmgroup.example</li>
      <li>27 Marlow Street Sunbury 3429</li>
      <li>0400 555 218 or 9555 0147</li>
    </ul>
  </div>
  <div class="footer-col" style="left:751px">
    <h3>Quick Links</h3>
    <ul><li>About us</li><li>Our Services</li><li>Testimonials</li><li>Why us</li><li>Contact Us</li></ul>
  </div>
  <div class="footer-col social" style="left:924px">
    <h3>Get In Touch</h3>
    <ul>
      <li><span class="social__dot"></span>Chatter</li>
      <li><span class="social__dot"></span>Friendly</li>
      <li><span class="social__dot"></span>Worklink</li>
      <li><span class="social__dot"></span>Snapshot</li>
    </ul>
  </div>
  <div class="footer-rule"></div>
  <p class="copyright">Copyright © 2019 All right reserved</p>
</footer>

</body>
</html>
```